Local fast-growing company in the service sector

We are looking for a modern business card design, which should also appear on our letterheads

Target Market(s)

Private and industrial sectors

Contact Information for Business Card

Vorname Name
Kellberger Str. 18
73614 Schorndorf
Tel.: 07146-839214-0
Name@agentur-kvtl.de

Colors
9d9d9d
919191
aaaaaa

Requirements
Must have
• The logo (file) in silver

```html
<!DOCTYPE html>
<html lang="de">
<head>
<meta charset="utf-8">
<title>KVTL Visitenkarte</title>
<link href="https://fonts.googleapis.com/css2?family=Open+Sans:wght@400;600;700;800&display=swap" rel="stylesheet">
<style>
  :root {
    --page-bg: #e6e4e1;
    --card-white: #ffffff;
    --silver-light: #d8d8d8;
    --silver-mid: #aaaaaa;
    --silver-dark: #919191;
    --band-dark: #4d4e50;
    --band-light: #9d9d9d;
    --text-dark: #4a4a4a;
    --text-logo-front: #111111;
    --text-logo-back: #9d9d9d;
    --card-shadow: 0 10px 28px rgba(0,0,0,0.22);
  }
  * { box-sizing: border-box; margin: 0; padding: 0; }
  html, body { width: 1200px; height: 900px; overflow: hidden; }
  body {
    background: var(--page-bg);
    font-family: "Open Sans", Arial, sans-serif;
    display: flex;
    align-items: center;
    justify-content: center;
    gap: 56px;
  }
  .card {
    position: relative;
    width: 520px;
    height: 336px;
    box-shadow: var(--card-shadow);
    overflow: hidden;
  }
  /* Front */
  .card-front {
    background: linear-gradient(115deg, var(--silver-dark) 0%, var(--silver-mid) 30%, var(--silver-light) 55%, var(--silver-mid) 78%, var(--silver-dark) 100%);
    display: flex;
    align-items: center;
    justify-content: center;
  }
  .brand {
    display: flex;
    align-items: center;
    gap: 14px;
  }
  .brand-mark {
    width: 26px;
    height: 26px;
    background: currentColor;
  }
  .brand-name {
    font-weight: 800;
    letter-spacing: 1px;
    line-height: 1;
  }
  .card-front .brand { color: var(--text-logo-front); }
  .card-front .brand-name { font-size: 64px; }
  .card-front .brand-mark { width: 34px; height: 34px; }

  /* Back */
  .card-back { background: var(--card-white); }
  .back-wave { position: absolute; inset: 0; }
  .holder-name {
    position: absolute;
    left: 36px;
    top: 52px;
    font-size: 17px;
    font-weight: 700;
    color: var(--text-dark);
    letter-spacing: 0.3px;
  }
  .card-back .brand {
    position: absolute;
    right: 34px;
    top: 46px;
    color: var(--text-logo-back);
  }
  .card-back .brand-name { font-size: 40px; }
  .card-back .brand-mark { width: 22px; height: 22px; }
  .contact {
    position: absolute;
    left: 36px;
    top: 150px;
    list-style: none;
    color: var(--text-dark);
    font-size: 14px;
    line-height: 21px;
  }
  .contact li { display: flex; align-items: center; gap: 8px; }
  .contact svg { width: 12px; height: 12px; fill: var(--text-dark); flex: none; }
  .contact .address { margin-top: 8px; }
</style>
</head>
<body>

  <section class="card card-front" aria-label="Visitenkarte Vorderseite">
    <div class="brand">
      <span class="brand-mark" aria-hidden="true"></span>
      <span class="brand-name">KVTL</span>
    </div>
  </section>

  <section class="card card-back" aria-label="Visitenkarte Rückseite">
    <svg class="back-wave" viewBox="0 0 520 336" preserveAspectRatio="none" aria-hidden="true">
      <path d="M0 336 L0 304 C150 330 280 255 380 186 C440 146 490 136 520 134 L520 336 Z" fill="var(--band-light)"/>
      <path d="M0 336 L0 318 C150 342 290 270 390 200 C450 160 495 150 520 148 L520 336 Z" fill="var(--card-white)"/>
      <path d="M60 336 C190 330 300 280 400 210 C455 172 495 158 520 156 L520 336 Z" fill="var(--band-dark)"/>
    </svg>

    <h1 class="holder-name">VORNAME NAME</h1>

    <div class="brand">
      <span class="brand-mark" aria-hidden="true"></span>
      <span class="brand-name">KVTL</span>
    </div>

    <ul class="contact">
      <li>
        <svg viewBox="0 0 24 24" aria-hidden="true"><path d="M6.6 10.8a15.1 15.1 0 0 0 6.6 6.6l2.2-2.2c.3-.3.7-.4 1-.2 1.1.4 2.3.6 3.6.6.6 0 1 .4 1 1V20c0 .6-.4 1-1 1A17 17 0 0 1 3 4c0-.6.4-1 1-1h3.5c.6 0 1 .4 1 1 0 1.3.2 2.5.6 3.6.1.3 0 .7-.2 1z"/></svg>
        <span>07146-839214-0</span>
      </li>
      <li>
        <svg viewBox="0 0 24 24" aria-hidden="true"><path d="M2 5h20v14H2z M3.5 6.5 12 13l8.5-6.5" fill="none" stroke="#4a4a4a" stroke-width="2"/></svg>
        <span>Name@agentur-kvtl.de</span>
      </li>
      <li>
        <svg viewBox="0 0 24 24" aria-hidden="true"><circle cx="12" cy="12" r="10"/></svg>
        <span>www.agentur-kvtl.de</span>
      </li>
      <li class="address">Kellberger Str. 18 73614 Schorndorf</li>
    </ul>
  </section>

</body>
</html>
```